Business card for wedding & event planning company

I'm looking for a well designed double sided business card to represent my wedding and event planning company.

It should include the fact we manage the following events:
Weddings, birthdays, conferences, product launches, fashion shows & conventions
in the following areas:
Wiltshire, Oxfordshire, Berkshire & London

My contact details to be included are:

Moira Stanwick
07514 283640
moira@bluefernevents.co.uk
www.bluefernevents.co.uk

My logo can be found at the following Filebarn location:
AI file: https://www.filebarn.example/s/k3mxpw8rt51bn7d/logo_sourcefile.ai
PNG file:
https://www.filebarn.example/s/h6qvlz2ncy90tue/logo_image.png

Target Market(s)

women aged 30-55

Industry/Entity Type

Wedding

Contact Information for Business Card

in the following areas:

Moira Stanwick
Event Planner
07514 283640

Font styles to use
Serif
Sans Serif
Script

Requirements
Must have
• Purple and white colour scheme
Should not have
• Black background
• Please don't submit any of the see-through business card designs.

```html
<!DOCTYPE html>
<html lang="en">
<head>
<meta charset="utf-8">
<title>Blue Fern Events – Business Card</title>
<link rel="stylesheet" href="https://fonts.googleapis.com/css2?family=Open+Sans:wght@400;600;700&display=swap">
<style>
  :root {
    --page: #e4e4e4;
    --card: #ffffff;
    --card-band: #f4ecf6;
    --purple: #8a2f97;
    --purple-soft: #9b38aa;
    --ink: #2e2a30;
    --white: #ffffff;
    --dove-shade: #e7d6ea;
    --font-text: "Open Sans", Arial, sans-serif;
  }
  * { box-sizing: border-box; margin: 0; padding: 0; }
  html, body { width: 1200px; height: 900px; overflow: hidden; }
  body {
    background: var(--page);
    font-family: var(--font-text);
    position: relative;
  }
  .card {
    position: absolute;
    left: 250px;
    width: 700px;
    height: 400px;
    background: var(--card);
    overflow: hidden;
    box-shadow: 0 6px 18px rgba(0,0,0,0.18);
  }
  .card--front { top: 35px; }
  .card--back { top: 465px; }

  /* Front */
  .brand {
    position: absolute;
    left: 40px;
    top: 50px;
    width: 280px;
    display: flex;
    flex-direction: column;
    align-items: center;
    gap: 12px;
  }
  .brand__mark {
    width: 66px;
    height: 66px;
    border-radius: 50%;
    background: var(--purple);
  }
  .brand__name {
    color: var(--purple-soft);
    font-weight: 600;
    font-size: 30px;
    line-height: 1.2;
    white-space: nowrap;
  }
  .contact-name {
    position: absolute;
    right: 40px;
    top: 88px;
    color: var(--purple-soft);
    font-weight: 700;
    font-size: 28px;
    line-height: 1.2;
    letter-spacing: 1px;
    text-transform: uppercase;
  }
  .contact-phone {
    position: absolute;
    right: 40px;
    top: 148px;
    color: var(--ink);
    font-size: 18px;
    line-height: 1.3;
    display: flex;
    align-items: center;
    gap: 8px;
  }
  .icon { width: 16px; height: 16px; fill: var(--purple-soft); flex: none; }

  .front-band {
    position: absolute;
    left: 0; right: 0;
    top: 222px;
    height: 124px;
    background: var(--card-band);
  }
  .web-list {
    position: absolute;
    left: 70px;
    top: 258px;
    list-style: none;
    color: var(--ink);
    font-size: 18px;
    line-height: 28px;
  }
  .web-list li { display: flex; align-items: center; gap: 10px; }

  .base-stripe {
    position: absolute;
    left: 0; right: 0;
    bottom: 0;
    height: 54px;
    background: var(--purple);
    box-shadow: 0 -8px 0 var(--white), 0 -11px 0 var(--purple);
  }

  /* Back */
  .dove-art {
    position: absolute;
    width: 110px;
    height: 80px;
    border-radius: 40% 60% 50% 50%;
    background: radial-gradient(ellipse at center, var(--dove-shade), transparent 70%);
  }
  .dove-art--left { left: 60px; top: 8px; }
  .dove-art--right { right: 20px; top: 70px; }

  .services {
    position: absolute;
    left: 0; right: 0;
    top: 62px;
    text-align: center;
    color: var(--ink);
    font-size: 18px;
    line-height: 25px;
  }
  .services__heading {
    color: var(--purple-soft);
    font-weight: 700;
    font-size: 17px;
    line-height: 24px;
  }
  .services__group + .services__group { margin-top: 20px; }
</style>
</head>
<body>

<section class="card card--front" aria-label="Business card front">
  <div class="front-band"></div>

  <div class="brand">
    <span class="brand__mark" aria-hidden="true"></span>
    <span class="brand__name">Blue Fern Events</span>
  </div>

  <h1 class="contact-name">Moira Stanwick</h1>
  <p class="contact-phone">07514 283640
    <svg class="icon" viewBox="0 0 24 24" aria-hidden="true"><path d="M6.6 10.8a15.1 15.1 0 0 0 6.6 6.6l2.2-2.2c.3-.3.7-.4 1-.2 1.1.4 2.3.6 3.6.6.6 0 1 .4 1 1V20c0 .6-.4 1-1 1A17 17 0 0 1 3 4c0-.6.4-1 1-1h3.5c.6 0 1 .4 1 1 0 1.3.2 2.5.6 3.6.1.3 0 .7-.2 1z"/></svg>
  </p>

  <ul class="web-list">
    <li>
      <svg class="icon" viewBox="0 0 24 24" aria-hidden="true"><path d="M2 5h20v14H2zm2 2v.5l8 5 8-5V7z"/></svg>
      moira@bluefernevents.co.uk
    </li>
    <li>
      <svg class="icon" viewBox="0 0 24 24" aria-hidden="true"><path d="M10.6 13.4a1 1 0 0 1 0-1.4l3-3a3 3 0 0 1 4.2 4.2l-2.5 2.5-1.4-1.4 2.5-2.5a1 1 0 0 0-1.4-1.4l-3 3a1 1 0 0 1-1.4 0zM13.4 10.6a1 1 0 0 1 0 1.4l-3 3a3 3 0 0 1-4.2-4.2l2.5-2.5 1.4 1.4-2.5 2.5a1 1 0 0 0 1.4 1.4l3-3a1 1 0 0 1 1.4 0z"/></svg>
      www.bluefernevents.co.uk
    </li>
  </ul>
  <div class="base-stripe"></div>
</section>

<section class="card card--back" aria-label="Business card back">
  <div class="dove-art dove-art--left" role="img" aria-label="Faint line illustration of a flying dove"></div>
  <div class="dove-art dove-art--right" role="img" aria-label="Faint line illustration of a flying dove"></div>

  <div class="services">
    <div class="services__group">
      <h2 class="services__heading">Events:</h2>
      <p>Weddings | Birthdays | Conferences |</p>
      <p>Product Launches | Fashion Shows</p>
    </div>
    <div class="services__group">
      <h2 class="services__heading">Convention Areas:</h2>
      <p>Wiltshire | Oxfordshire | Berkshire | London</p>
    </div>
  </div>
  <div class="base-stripe"></div>
</section>

</body>
</html>
```